Resposive web site in 4 languages + image gallery + logo design

We need a web page, which will work on all devices.
I have uploaded web page concept.
Company name: Praxelun
Industry/Entity Type
It Company
Logo Text
quality matters
Coding
Coded - Design and coding required
Number of Pages Required
1 page

```html
<!DOCTYPE html>
<html lang="en">
<head>
<meta charset="utf-8">
<title>Praxelun</title>
<link rel="stylesheet" href="https://fonts.googleapis.com/css2?family=Questrial&family=Lato:wght@400;700&display=swap">
<style>
:root{
  --ink:#222;
  --text:#333;
  --line:#555;
  --white:#fff;
  --wood-dark:#2a160c;
  --wood-mid:#5a3420;
  --panel:#3b3b3b;
  --panel-edge:#4a4a4a;
  --footer:#2e2e2e;
  --bottom:#1c1c1c;
  --muted:#cfcfcf;
  --accent-blue:#3b5998;
}
*{box-sizing:border-box;margin:0;padding:0}
html,body{width:1200px;height:2329px;overflow:hidden;background:var(--white)}
body{position:relative;font-family:"Lato",sans-serif;color:var(--text)}
.abs{position:absolute}
.heading{font-family:"Questrial",sans-serif;font-weight:400}

/* header */
.site-header{left:0;top:0;width:1200px;height:87px;background:var(--white)}
.brand{left:130px;top:26px;font-family:"Questrial",sans-serif;font-size:34px;color:var(--ink);letter-spacing:1px;display:flex;align-items:center;gap:10px}
.brand-mark{width:12px;height:12px;background:var(--ink)}
.main-nav a{position:absolute;top:44px;font-size:16px;color:var(--ink);text-decoration:none;text-transform:uppercase}
.main-nav a.active{border-bottom:2px solid var(--ink);padding-bottom:7px}
.lang-flag{left:905px;top:43px;width:44px;height:22px;background:linear-gradient(#23387a,#c8102e 50%,#23387a)}
.lang-caret{left:958px;top:51px}
.like-btn{left:998px;top:40px;width:70px;height:28px;background:var(--accent-blue);border-radius:3px;color:var(--white);font-size:15px;font-weight:700;text-align:center;line-height:28px}

/* hero */
.hero{left:0;top:87px;width:1200px;height:497px;background:linear-gradient(90deg,#6d6a66 0%,#8a5a3a 30%,#a0683f 50%,#8b5e40 65%,#cfd3d4 85%,#e8ecee 100%)}
.hero-title{left:0;top:315px;width:1200px;text-align:center;color:var(--white);font-family:"Lato",sans-serif;font-weight:700;font-size:37px;text-shadow:0 2px 4px rgba(0,0,0,.5)}
.hero-btn{left:506px;top:373px;width:188px;height:55px;border:2px solid var(--white);color:var(--white);font-weight:700;font-size:18px;text-align:center;line-height:51px;background:rgba(0,0,0,.15)}
.slide-arrow{top:317px;width:40px;height:37px;background:#333;display:flex;align-items:center;justify-content:center}

/* section titles */
.sec-title{left:0;width:1200px;text-align:center;font-size:31px}
.divider{left:283px;width:635px;height:12px}

/* welcome */
.welcome-text{left:158px;top:707px;width:884px;text-align:center;font-size:15px;line-height:25.6px;color:var(--text)}
.outline-btn{left:533px;top:829px;width:133px;height:36px;border:1.5px solid var(--ink);font-size:15px;font-weight:700;text-align:center;line-height:33px;color:var(--ink)}

/* featured */
.featured{left:0;top:913px;width:1200px;height:472px;background:linear-gradient(90deg,#2a160c,#5a3420 20%,#3a1f10 45%,#5e3822 70%,#2c170c)}
.service{width:296px;color:var(--white);text-align:center}
.service-photo{width:296px;height:180px;border:7px solid var(--white)}
.service h3{margin-top:25px;font-family:"Lato",sans-serif;font-weight:700;font-size:22px;letter-spacing:1px}
.service p{margin:18px auto 0;width:270px;font-size:15px;line-height:20.5px}

/* gallery */
.filters{left:0;top:1501px;width:1200px;display:flex;justify-content:center;gap:34px;font-size:15px;color:var(--text)}
.filter{display:flex;align-items:center;gap:10px}
.box{width:17px;height:17px;border:1.5px solid #555;display:flex;align-items:center;justify-content:center}
.thumb{top:1550px;width:219px;height:142px;border:1px solid #999;padding:4px;background:var(--white)}
.thumb-fill{width:100%;height:100%}
.thumb-overlay{position:absolute;inset:4px;background:rgba(60,60,60,.75);color:var(--white);text-align:center;padding-top:36px}
.thumb-overlay b{display:block;font-size:15px;margin-bottom:10px}
.thumb-overlay span{font-size:13px;line-height:19px;display:block}

/* contact band */
.contact-band{left:0;top:1741px;width:1200px;height:341px;background:var(--panel)}
.band-title{font-family:"Lato",sans-serif;font-size:20px;color:var(--white);text-transform:uppercase;letter-spacing:.5px}
.band-rule{height:0;border-top:1px dotted #888}
.field{background:var(--white);font-size:12.5px;color:#555;padding:6px 8px}
.submit-btn{left:132px;top:2015px;width:84px;height:31px;border:1.5px solid var(--white);color:var(--white);font-size:13px;font-weight:700;text-align:center;line-height:28px}
.quote-bubble{left:629px;top:1832px;width:439px;height:152px;background:var(--white);border-radius:8px;padding:18px 22px 0 60px;font-style:italic;font-size:13px;line-height:22px;color:#444}
.quote-tail{left:820px;top:1982px}
.avatar{left:655px;top:1971px;width:74px;height:74px;border-radius:50%;background:linear-gradient(#b98a6a,#7a5a48);border:4px solid var(--white)}
.quote-name{left:748px;top:2007px;font-size:14px;font-weight:700;color:var(--white)}

/* footer */
.site-footer{left:0;top:2082px;width:1200px;height:210px;background:var(--footer)}
.foot-title{font-family:"Questrial",sans-serif;font-size:19px;color:var(--white)}
.foot-rule{height:0;border-top:1px dotted #777}
.foot-sep{top:2120px;width:0;height:135px;border-left:1px solid #444}
.foot-links li{list-style:none;font-size:13px;color:var(--muted);height:26.5px}
.foot-links li::before{content:"›";margin-right:10px}
.contact-row{display:flex;gap:14px;font-size:13px;color:var(--muted);line-height:18px}
.map{left:613px;top:2160px;width:173px;height:88px;background:linear-gradient(135deg,#cfe3ef,#e9e3c8 50%,#bcd6e6);border:3px solid var(--white)}
.foot-brand{left:880px;top:2175px;font-family:"Questrial",sans-serif;font-size:32px;color:#777;letter-spacing:1px}
.copyright{left:0;top:2292px;width:1200px;height:37px;background:var(--bottom);color:var(--muted);font-size:12.5px;text-align:center;line-height:37px}
</style>
</head>
<body>

<header class="abs site-header">
  <div class="abs brand"><span class="brand-mark"></span>PRAXELUN</div>
  <nav class="main-nav">
    <a class="active" style="left:470px">Home</a>
    <a style="left:553px">Services</a>
    <a style="left:658px">About Us</a>
    <a style="left:772px">Contact Us</a>
  </nav>
  <div class="abs lang-flag" role="img" aria-label="English language flag"></div>
  <svg class="abs lang-caret" width="10" height="6"><path d="M0 0h10L5 6z" fill="#222"/></svg>
  <div class="abs like-btn">Like</div>
</header>

<section class="abs hero" role="img" aria-label="Bright living room with a wood-panelled wall, armchairs and large windows"></section>
<h1 class="abs hero-title">Are you interested in an estimate?</h1>
<div class="abs hero-btn">GET A QUOTE</div>
<div class="abs slide-arrow" style="left:6px"><svg width="10" height="14"><path d="M8 1L2 7l6 6" stroke="#fff" stroke-width="2.5" fill="none"/></svg></div>
<div class="abs slide-arrow" style="left:1154px"><svg width="10" height="14"><path d="M2 1l6 6-6 6" stroke="#fff" stroke-width="2.5" fill="none"/></svg></div>

<h2 class="abs heading sec-title" style="top:622px;color:var(--ink)">Welcome to PRAXELUN</h2>
<svg class="abs divider" style="top:677px"><line x1="0" y1="6" x2="635" y2="6" stroke="#555"/><circle cx="317" cy="6" r="5" fill="#222"/></svg>
<p class="abs welcome-text">Praxelun is a company whose business operations include making wooden products, restoration and building structures from natural stone. All of our products are made by craftsmen and specialists who have extensive experience and knowledge in their fields. The products we offer are always handmade and we take the requests and ideas of the specific client into account We always strive to achieve the best possible quality.</p>
<div class="abs outline-btn">READ MORE</div>

<section class="abs featured" role="img" aria-label="Dark wood plank background"></section>
<h2 class="abs heading sec-title" style="top:948px;color:var(--white)">Featured Services</h2>
<svg class="abs divider" style="top:1003px"><line x1="0" y1="6" x2="635" y2="6" stroke="#ddd"/><circle cx="317" cy="6" r="5" fill="#fff"/></svg>

<article class="abs service" style="left:132px;top:1039px">
  <div class="service-photo" role="img" aria-label="Wooden staircase and hardwood floor interior" style="background:linear-gradient(135deg,#c9b9a4,#8c4a22 60%,#5a2e14)"></div>
  <h3>WOODWORKS</h3>
  <p>Timber is, in essence, a natural and warm material. Wood is also relatively durable and easy to work with... [+]</p>
</article>
<article class="abs service" style="left:452px;top:1039px">
  <div class="service-photo" role="img" aria-label="Kitchen with stone countertop and stone column" style="background:linear-gradient(135deg,#e8e6e2,#b8aa98 55%,#8a7560)"></div>
  <h3>STONE WORKS</h3>
  <p>The natural stone found in the ground has been used in construction for centuries because of its durability... [+]</p>
</article>
<article class="abs service" style="left:772px;top:1039px">
  <div class="service-photo" role="img" aria-label="Workers restoring a wooden house facade on a ladder" style="background:linear-gradient(90deg,#b06a3a,#c98a55 60%,#6f8f4a)"></div>
  <h3>RESTORATION</h3>
  <p>It's good to see that fixing old things has become popular again in recent years and people... [+]</p>
</article>

<h2 class="abs heading sec-title" style="top:1423px;color:var(--ink)">Projects Gallery</h2>
<svg class="abs divider" style="top:1472px"><line x1="0" y1="6" x2="635" y2="6" stroke="#555"/><circle cx="317" cy="6" r="5" fill="#222"/></svg>
<div class="abs filters">
  <span class="filter"><span class="box"><svg width="11" height="9"><path d="M1 4l3 3 6-6" stroke="#222" stroke-width="1.8" fill="none"/></svg></span>All</span>
  <span class="filter"><span class="box"></span>Woodworks</span>
  <span class="filter"><span class="box"></span>Stone Works</span>
  <span class="filter"><span class="box"></span>Restoration</span>
</div>
<svg class="abs" style="left:90px;top:1610px" width="12" height="22"><path d="M10 1L2 11l8 10" stroke="#222" stroke-width="2.5" fill="none"/></svg>
<svg class="abs" style="left:1099px;top:1610px" width="12" height="22"><path d="M2 1l8 10-8 10" stroke="#222" stroke-width="2.5" fill="none"/></svg>
<div class="abs thumb" style="left:132px"><div class="thumb-fill" role="img" aria-label="Living room at dusk with framed art" style="background:linear-gradient(#3a3e4a,#2a2420 60%,#6a5a4a)"></div></div>
<div class="abs thumb" style="left:371px;box-shadow:0 3px 8px rgba(0,0,0,.4)"><div class="thumb-fill" role="img" aria-label="Interior project photo" style="background:linear-gradient(#7a7a7a,#4a4a4a)"></div>
  <div class="thumb-overlay"><b>Lorem ipsum dolor</b><span>Lorem ipsum dolor sit amet<br>consectetur adipiscing elit.</span></div></div>
<div class="abs thumb" style="left:610px"><div class="thumb-fill" role="img" aria-label="Dark wood kitchen with pendant lights" style="background:linear-gradient(#3a2a22,#6a5040 55%,#2a1e18)"></div></div>
<div class="abs thumb" style="left:849px"><div class="thumb-fill" role="img" aria-label="Chandelier in a purple-lit room" style="background:linear-gradient(135deg,#4a3a6a,#8a6a5a 55%,#3a2e4e)"></div></div>

<section class="abs contact-band"></section>
<h3 class="abs band-title" style="left:130px;top:1776px">Get in touch with us</h3>
<div class="abs band-rule" style="left:130px;top:1814px;width:438px"></div>
<p class="abs" style="left:130px;top:1827px;font-size:13px;color:var(--white)">Lorem ipsum dolor sit amet consectetuer adipiscing sed dmmy nibh</p>
<div class="abs field" style="left:132px;top:1860px;width:207px;height:28px">First Name</div>
<div class="abs field" style="left:359px;top:1860px;width:208px;height:28px">Last Name</div>
<div class="abs field" style="left:132px;top:1897px;width:207px;height:28px">Email</div>
<div class="abs field" style="left:359px;top:1897px;width:208px;height:28px">Phone</div>
<div class="abs field" style="left:132px;top:1935px;width:435px;height:65px">Your Message</div>
<div class="abs submit-btn">SUBMIT</div>

<h3 class="abs band-title" style="left:629px;top:1776px">Client Testimonials</h3>
<svg class="abs" style="left:1038px;top:1781px" width="32" height="14"><path d="M7 1L1 7l6 6M25 1l6 6-6 6" stroke="#ddd" stroke-width="1.6" fill="none"/></svg>
<div class="abs band-rule" style="left:629px;top:1814px;width:439px"></div>
<div class="abs quote-bubble">
  <svg class="abs" style="left:22px;top:18px" width="28" height="22"><path d="M2 22l6-20h6L9 22zM14 22l6-20h6l-5 20z" fill="#ccc"/></svg>
  Lorem ipsum dolor sit amet consetug e sed diay nibh euismodl tincidunt ut laoreet dolore magam er vol wisi enim ad minim veniam quis nostrud exerci tationorem ipsum dolor sit ametee sed diammmy nibh euismd tincidunt ut laoreet dolore magna aliqur volpatl tiidunt ut laoreet dolore magna aliqur volpatl
</div>
<svg class="abs quote-tail" width="70" height="26"><path d="M0 0h70L40 24z" fill="#fff"/></svg>
<div class="abs avatar" role="img" aria-label="Client portrait"></div>
<div class="abs quote-name">Mr. Elric Dawsonfield</div>

<footer class="abs site-footer"></footer>
<div class="abs foot-sep" style="left:295px"></div>
<div class="abs foot-sep" style="left:572px"></div>
<div class="abs foot-sep" style="left:832px"></div>

<h4 class="abs foot-title" style="left:130px;top:2117px">Quick Links</h4>
<div class="abs foot-rule" style="left:130px;top:2148px;width:110px"></div>
<ul class="abs foot-links" style="left:132px;top:2158px">
  <li>Home</li><li>Services</li><li>About Us</li><li>Contact Us</li>
</ul>

<h4 class="abs foot-title" style="left:345px;top:2117px">Contact Information</h4>
<div class="abs foot-rule" style="left:345px;top:2148px;width:170px"></div>
<div class="abs contact-row" style="left:346px;top:2156px">
  <svg width="12" height="16"><path d="M6 0a6 6 0 0 0-6 6c0 4 6 10 6 10s6-6 6-10a6 6 0 0 0-6-6z" fill="#ddd"/><circle cx="6" cy="6" r="2.2" fill="#2e2e2e"/></svg>
  <span>Varela 12 40210 Norvik<br>LUMERIA</span>
</div>
<div class="abs contact-row" style="left:346px;top:2202px">
  <svg width="12" height="14"><path d="M2 1l3 0 1 4-2 1.5a8 8 0 0 0 3.5 3.5L9 8l4 1v3c-6 1-12-5-11-11z" fill="#ddd"/></svg>
  <span>014-552-7310</span>
</div>
<div class="abs contact-row" style="left:346px;top:2233px">
  <svg width="13" height="12" style="margin-top:3px"><rect x="0" y="1" width="13" height="9" fill="#ddd"/><path d="M0 1l6.5 5L13 1" stroke="#2e2e2e" fill="none"/></svg>
  <span>sales@praxelun.com</span>
</div>

<h4 class="abs foot-title" style="left:612px;top:2119px">Location Map</h4>
<div class="abs foot-rule" style="left:612px;top:2148px;width:175px"></div>
<div class="abs map" role="img" aria-label="Street map showing the office location"></div>

<div class="abs foot-brand">PRAXELUN</div>

<div class="abs copyright">Copyright © 2016 PRAXELUN.&nbsp; All Rights Reserved.</div>

</body>
</html>
```